Unique Builder wordpress website - Supply Graphics Only

We need a brand new website for a building company in Perth, Australia who constructs insulated panels (sip).
What is a SIP?
A SIP is a high-performance building panel used for floors, walls, and roofs in residential and commercial buildings. Panels are typically made using Expanded Polystyrene (EPS) sandwiched between two structural skins.
The design must incorporate a slick professional look and keep to the logo colours (Lime green & Blacks). The logo must not change colours or be altered. (
We will convert the graphics to a wordpress site. We have our own coders)
Design:
The website design must be clean, mobile friendly and the final design will be adapted to WordPress CMS.
The menus must contain dropdown menus and front page may contain a youtube video at a later date.
Fonts must be clear and easy to read
The contact us page will need to have an online form and google map.
The 16 pages listed will be the complete site and are for reference only. For this project the winning designer would need to supply the Homepage, and 1 inner pages only as PSD files.
The structure is as follows:
Home
About us
Marlow Fen Dwellings
What is a sip
Benefits
FAQ
Designs
Residential
Granny Flats
Architectural design
Photo Gallery <--- Would be great if a sample design can be provided
Services
Project management and custom design
Site Assembly
Kit Supply
Contact us
***We don't need the designer to design every page however a 1 inner page would be ideal****
Our Competitors websites
Note: the following websites look crap however, the following websites are some of our competitors. We want a clean and awesome layout.
http://www.corvamoda.com.au/
http://dralventorix.com.au/
http://www.quilbarrow.net.au/
New home builders and commercial builders
Building
5+ page

```html
<!DOCTYPE html>
<html lang="en">
<head>
<meta charset="utf-8">
<title>Panelcrest – Home</title>
<link href="https://fonts.googleapis.com/css2?family=Raleway:wght@300;400;500;600;700;800&display=swap" rel="stylesheet">
<style>
:root{
  --lime:#b3d233;
  --lime-soft:#c8e06a;
  --yellow:#e6e62a;
  --ink:#1b1b1b;
  --dark:#232323;
  --dark-2:#2e2e2e;
  --dark-3:#3a3a3a;
  --stage:#1a1a1a;
  --white:#ffffff;
  --paper:#e9e9e9;
  --grey:#8a8a8a;
  --grey-light:#bdbdbd;
}
*{margin:0;padding:0;box-sizing:border-box}
html,body{width:1200px;height:1200px;overflow:hidden;background:var(--stage);font-family:"Raleway",sans-serif}
.page{position:absolute;left:353px;top:0;width:617px;height:1500px;transform:scale(.8);transform-origin:0 0;overflow:hidden;background:var(--dark)}
.abs{position:absolute}
section{position:absolute;left:0;width:617px}

/* hero */
.hero{top:0;height:284px;background:var(--dark-2)}
.hero-photo{position:absolute;inset:0;background:radial-gradient(ellipse at 60% 55%,#4a4a4a 0%,#333 45%,#262626 100%)}
.brand{left:99px;top:14px;display:flex;align-items:center;gap:5px;color:var(--white);font-size:10px;font-weight:600;line-height:12px}
.brand-mark{width:9px;height:9px;background:var(--lime)}
.main-nav{left:207px;top:19px;display:flex;gap:11px;font-size:5px;letter-spacing:.3px;color:var(--grey-light)}
.nav-rule{left:99px;top:43px;width:418px;height:2px;background:var(--lime)}
.quick{left:99px;top:58px;display:flex;gap:9px;font-size:3.6px;color:var(--grey-light)}
.quick .label{color:var(--lime)}
.socials{display:flex;gap:5px}
.socials span{width:9px;height:9px;border-radius:50%;background:#555}
.hero-title{top:110px;width:617px;text-align:center;color:var(--lime);font-size:14px;font-weight:600}
.hero-sub{top:136px;width:617px;text-align:center;color:#9a9a9a;font-size:7.5px;line-height:11.5px;font-weight:300}
.btn{border-radius:8px;background:var(--lime);color:var(--ink);font-size:4.5px;font-weight:600;display:flex;align-items:center;justify-content:center}
.hero-btn{left:271px;top:172px;width:74px;height:13px}
.arrow{top:139px;width:12px;height:14px}

/* features */
.features{top:284px;height:182px;background:var(--white)}
.feature{position:absolute;top:-10px;width:62px;text-align:center}
.feature-icon{width:21px;height:21px;border-radius:50%;background:var(--lime);border:2px solid #fff;margin:0 auto;display:flex;align-items:center;justify-content:center}
.feature-icon i{width:7px;height:7px;border:1.2px solid #fff;border-radius:50%}
.feature h3{font-size:6px;font-weight:500;color:var(--lime);margin-top:10px;padding-bottom:10px;border-bottom:1px solid #d9ebb0}
.feature p{font-size:4.6px;line-height:9.2px;color:#555;margin-top:9px;padding:0 6px}
.swatches{left:14px;top:24px;width:24px}
.swatches span{display:block;width:24px;height:21px;margin-bottom:2px}

/* about */
.about{top:466px;height:240px;background:var(--dark-3)}
.about-left{left:0;top:0;width:207px;height:240px;background:var(--dark)}
.about-copy{left:100px;top:37px;width:100px;color:#c4c4c4;font-size:11.5px;line-height:17.5px;font-weight:300}
.about-copy b,.about-lead b{color:var(--lime);font-weight:400}
.about-lead{left:239px;top:38px;width:280px;color:#9a9a9a;font-size:8.5px;line-height:11.5px;font-weight:300}
.benefits{left:241px;top:84px;list-style:none}
.benefits li{display:flex;align-items:center;height:23.3px;color:#bdbdbd;font-size:7px;font-weight:300}
.benefits li svg{width:16px;height:14px;margin-right:12px}
.benefits small{font-size:4px;margin-left:3px}
.panel-photo{left:490px;top:50px;width:127px;height:125px;background:linear-gradient(160deg,#f4f4f4,#bfbfbf);clip-path:polygon(100% 0,100% 100%,20% 70%,0 50%)}

/* gallery */
.gallery{top:706px;height:243px;border-top:2px solid var(--yellow);display:grid;grid-template-columns:repeat(4,154.25px);grid-template-rows:120px 121px}
.tile{background:linear-gradient(135deg,#eee,#9d9d9d)}
.tile.dark{background:linear-gradient(135deg,#8a8a8a,#3d3d3d)}
.tile.warm{background:linear-gradient(135deg,#efe9de,#a99d8c)}
.tile.pool{background:linear-gradient(180deg,#5d5142,#3c4c63)}
.tile.feature-tile{background:var(--yellow);position:relative;display:flex;flex-direction:column;align-items:center;justify-content:center;gap:14px}
.tile-icons{display:flex;gap:6px;align-items:center}
.tile-icons span{width:13px;height:13px;border-radius:50%;border:1.5px solid #fff}
.tile-caption{color:#fff;font-size:5.5px;font-weight:700}

/* testimonial */
.testimonial{top:949px;height:204px;background:var(--paper)}
.quote-mark{top:22px;width:617px;text-align:center;color:var(--lime);font-size:44px;font-weight:800;line-height:44px}
.quote{top:64px;width:617px;text-align:center;color:#8d8d8d;font-size:8px;line-height:11px;font-weight:300}
.rule{top:115px;height:1px;background:#d0d0d0}
.rule::after{content:"";position:absolute;top:-1.5px;width:4px;height:4px;border-radius:50%;background:var(--lime)}
.rule.left{left:94px;width:180px}.rule.left::after{left:0}
.rule.right{left:343px;width:180px}.rule.right::after{right:0}
.avatar{left:291px;top:99px;width:35px;height:35px;border-radius:50%;background:linear-gradient(#b5b5b5,#6d6d6d);border:2px solid #fff}
.author{top:140px;width:617px;text-align:center;font-size:5px;line-height:8.5px;color:#444}
.author b{color:var(--lime);font-weight:500;display:block}
.dots{top:170px;left:295px;display:flex;gap:3px}
.dots span{width:4px;height:4px;border-radius:50%;border:.8px solid var(--lime)}
.dots span.on{background:var(--lime)}

/* stats */
.stats{top:1153px;height:83px;background:var(--lime)}
.stat{position:absolute;top:15px;width:70px;text-align:center;color:var(--ink)}
.stat svg{width:18px;height:16px}
.stat strong{display:block;font-size:14px;font-weight:800;line-height:17px;font-variant-numeric:oldstyle-nums}
.stat span{display:block;font-size:4.6px;font-weight:600;line-height:6.5px;margin-top:1px}

/* contact */
.contact{top:1236px;height:264px;background:#202020}
.contact h2{left:99px;top:31px;color:var(--lime);font-size:11px;font-weight:500}
.chev{left:261px;top:34px;width:11px;height:8px}
.field{border:1px solid #4a4a4a;border-radius:6px;font-size:3.8px;color:#777;padding:4px 6px}
.divider{left:307px;top:29px;width:2px;height:180px;background:var(--lime)}
.agree{left:99px;top:194px;display:flex;align-items:center;gap:8px;color:var(--lime);font-size:4.2px}
.agree i{width:5px;height:5px;border-radius:50%;background:var(--lime)}
.map-area{left:345px;top:52px;width:175px;height:140px;background:radial-gradient(ellipse at 65% 55%,#b3d233 0%,#8fad1f 45%,rgba(32,32,32,0) 70%)}
.address{left:351px;top:86px;width:125px;height:86px;background:rgba(45,45,45,.96);border:1px solid #555;border-radius:4px;color:#ddd;font-size:4.2px;line-height:10.5px;padding:6px 8px 0 20px}
.address .pin{position:absolute;left:9px;width:5px;height:5px;border-radius:50%;background:var(--lime)}
.footnote{left:99px;top:238px;font-size:3.8px;color:#666}
.top-btn{left:302px;top:229px;width:13px;height:13px;border-radius:50%;border:1px solid #555}
</style>
</head>
<body>
<div class="page">

  <section class="hero">
    <div class="hero-photo" role="img" aria-label="Dark photo of architectural plans with a pen"></div>
    <div class="abs brand"><span class="brand-mark"></span>Panelcrest</div>
    <nav class="abs main-nav">
      <span>ABOUT US</span><span>BENEFITS</span><span>PROJECTS</span><span>FAQ</span><span>GALLERY</span><span>SERVICES</span><span>CONTACT US</span><span>RESOURCES</span>
      <svg width="7" height="7" viewBox="0 0 8 8"><circle cx="3.3" cy="3.3" r="2.5" fill="none" stroke="#bdbdbd"/><path d="M5.2 5.2 7.5 7.5" stroke="#bdbdbd"/></svg>
    </nav>
    <div class="abs nav-rule"></div>
    <div class="abs quick">
      <span class="label">QUICKLINKS</span><span>SITE ASSEMBLY</span><span>KIT SUPPLY</span><span>PROJECT MANAGEMENT AND CUSTOM DESIGN</span><span>MARLOW FEN DWELLINGS</span><span>WHAT IS A SIP</span>
    </div>
    <div class="abs socials" style="left:439px;top:55px"><span></span><span></span><span></span><span></span><span></span></div>
    <h1 class="abs hero-title">Get Your Free SIPS Info Pack</h1>
    <p class="abs hero-sub">Find out the 10 ways SIPS panels can benefit your project.<br>Download the free info pack now.</p>
    <div class="abs btn hero-btn">DOWNLOAD&nbsp;<b>NOW</b></div>
    <svg class="abs arrow" style="left:98px" viewBox="0 0 12 14"><path d="M8 2 3 7l5 5" fill="none" stroke="#fff" stroke-width="1.8"/></svg>
    <svg class="abs arrow" style="left:507px" viewBox="0 0 12 14"><path d="M4 2l5 5-5 5" fill="none" stroke="#fff" stroke-width="1.8"/></svg>
  </section>

  <section class="features">
    <div class="abs swatches">
      <span style="background:var(--lime)"></span><span style="background:#000"></span><span style="background:#333"></span><span style="background:#fff"></span><span style="background:var(--lime-soft)"></span><span style="background:var(--yellow)"></span>
    </div>
    <div class="feature" style="left:99px"><div class="feature-icon"><i></i></div><h3>Safety</h3><p>We offer a unique design and project delivery service to develop your specific building requirements.</p></div>
    <div class="feature" style="left:170px"><div class="feature-icon"><i></i></div><h3>Productivity</h3><p>House designs can be selected from our standard designs or can form the basis of your unique design. We understand each site is different with you to optimize your design.</p></div>
    <div class="feature" style="left:241px"><div class="feature-icon"><i></i></div><h3>Flexibility</h3><p>We offer a professional custom design service so bring us your thoughts and we will turn them into a building for you.</p></div>
    <div class="feature" style="left:313px"><div class="feature-icon"><i></i></div><h3>Accuracy</h3><p>Our team can arrange for the supply of a basic wall kit to full turn key build in accordance with all building license requirements.</p></div>
    <div class="feature" style="left:384px"><div class="feature-icon"><i></i></div><h3>Efficiency</h3><p>Our team supplies wall panel building kits to builders, developers and owner builders for use in residential and commercial buildings that are fully compliant to Australian standards.</p></div>
    <div class="feature" style="left:456px"><div class="feature-icon"><i></i></div><h3>Adaptability</h3><p>All orders have a detailed bill of materials together with a set of panel wall build instruction and recommendations.</p></div>
  </section>

  <section class="about">
    <div class="abs about-left"></div>
    <p class="abs about-copy"><b>panelcrest</b> are designers and manufacturers of an engineered structural insulated panel and concealed structural frame building product.</p>
    <p class="abs about-lead"><b>sips</b> is rapidly becoming the building method of choice because of its overwhelming benefits and proven suitability.</p>
    <ul class="abs benefits">
      <li><svg viewBox="0 0 16 14"><path d="M1 13 6 3l4 7 2-3 3 6z" fill="none" stroke="#ddd"/></svg>High level of captive insulation.<small>(warm in winter cool in summer)</small></li>
      <li><svg viewBox="0 0 16 14"><ellipse cx="8" cy="8" rx="6" ry="4" fill="#ddd"/></svg>Very strong, light weight and durable.</li>
      <li><svg viewBox="0 0 16 14"><circle cx="11" cy="2.5" r="1.6" fill="#ddd"/><path d="M3 13l4-4 2 2 1-5-4 1M9 6l4 3" fill="none" stroke="#ddd" stroke-width="1.3"/></svg>20 + year history of performance in cyclonic locations in WA</li>
      <li><svg viewBox="0 0 16 14"><circle cx="8" cy="7" r="6" fill="none" stroke="#ddd"/><path d="M8 3v4h3" fill="none" stroke="#ddd"/></svg>Reduced build time<small>(save time save money it's that easy)</small></li>
      <li><svg viewBox="0 0 16 14"><path d="M8 1 13 5 8 13 3 5z" fill="none" stroke="#ddd"/></svg>Energy efficient<small>(less energy to build and less energy to run ie lower power bills)</small></li>
    </ul>
    <div class="abs panel-photo" role="img" aria-label="White insulated wall panel"></div>
  </section>

  <section class="gallery">
    <div class="tile" role="img" aria-label="Bright open-plan office interior"></div>
    <div class="tile feature-tile">
      <div class="tile-icons"><span></span><span style="margin-top:-14px"></span><span></span></div>
      <div class="tile-caption">LOREM IPSUM</div>
    </div>
    <div class="tile dark" role="img" aria-label="Builder in hard hat installing panels"></div>
    <div class="tile" role="img" aria-label="Modern white living room"></div>
    <div class="tile" role="img" aria-label="White dining and kitchen interior"></div>
    <div class="tile warm" role="img" aria-label="Builders working on a site plan"></div>
    <div class="tile pool" role="img" aria-label="Modern house with pool at dusk"></div>
    <div class="tile warm" role="img" aria-label="Minimal hallway with garden view"></div>
  </section>

  <section class="testimonial">
    <div class="abs quote-mark">“</div>
    <p class="abs quote">Whatever settling goodness too and honoured she building answered<br>her. Strongly thoughts remember mr to do consider debating</p>
    <div class="abs rule left"></div>
    <div class="abs rule right"></div>
    <div class="abs avatar" role="img" aria-label="Portrait of the client"></div>
    <p class="abs author"><b>Mara Ellison</b>CEO Ferndale - Lorem Ipsum</p>
    <div class="abs dots"><span></span><span></span><span class="on"></span><span></span></div>
  </section>

  <section class="stats">
    <div class="stat" style="left:95px"><svg viewBox="0 0 18 16"><path d="M3 7h10v3a4 4 0 0 1-4 4H7a4 4 0 0 1-4-4z M13 8h2v2h-2" fill="#1b1b1b"/></svg><strong>8950</strong><span>CUPS OF<br>COFFEE</span></div>
    <div class="stat" style="left:165px"><svg viewBox="0 0 18 16"><path d="M6 2v12M12 2v12M4 5l2 2 2-2M10 5l2 2 2-2" fill="none" stroke="#1b1b1b" stroke-width="1.6"/></svg><strong>24</strong><span>INTERNATIONAL<br>AWARDS</span></div>
    <div class="stat" style="left:236px"><svg viewBox="0 0 18 16"><path d="M3 7h3v7H3zM7 14V7l3-5 1 1-1 4h5v3l-2 4z" fill="#1b1b1b"/></svg><strong>55K</strong><span>SOCIAL<br>LIKES</span></div>
    <div class="stat" style="left:308px"><svg viewBox="0 0 18 16"><circle cx="9" cy="8" r="6.5" fill="none" stroke="#1b1b1b" stroke-width="1.5"/><path d="M2.5 8h13M9 1.5v13" stroke="#1b1b1b"/></svg><strong>89</strong><span>OFFICES<br>WORLDWIDE</span></div>
    <div class="stat" style="left:379px"><svg viewBox="0 0 18 16"><path d="M9 3l1.6 3.3 3.4.4-2.5 2.4.7 3.4L9 10.8l-3.2 1.7.7-3.4L4 6.7l3.4-.4z" fill="#1b1b1b"/></svg><strong>20</strong><span>YEARS OF<br>EXCELLENCE</span></div>
    <div class="stat" style="left:452px"><svg viewBox="0 0 18 16"><circle cx="6" cy="6" r="3" fill="#1b1b1b"/><path d="M1 15a5 5 0 0 1 10 0z" fill="#1b1b1b"/><rect x="11" y="2" width="6" height="4" rx="1" fill="#1b1b1b"/></svg><strong>709</strong><span>CLIENTS<br>SERVED</span></div>
  </section>

  <section class="contact">
    <h2 class="abs">Get in touch</h2>
    <svg class="abs chev" viewBox="0 0 11 8"><path d="M1 1.5 5.5 6 10 1.5" fill="none" stroke="#b3d233" stroke-width="1.6"/></svg>
    <div class="abs field" style="left:99px;top:60px;width:87px;height:14px">NAME</div>
    <div class="abs field" style="left:197px;top:60px;width:81px;height:14px">EMAIL</div>
    <div class="abs field" style="left:99px;top:84px;width:179px;height:14px">SUBJECT</div>
    <div class="abs field" style="left:99px;top:108px;width:179px;height:72px">MESSAGE</div>
    <div class="abs agree"><i></i>Yes, you can sent me e-mail</div>
    <div class="abs btn" style="left:192px;top:192px;width:42px;height:11px">RESET</div>
    <div class="abs btn" style="left:237px;top:192px;width:41px;height:11px">SUBMIT</div>
    <div class="abs divider"></div>
    <div class="abs map-area" role="img" aria-label="Map of Australia with office location pins"></div>
    <div class="abs address">
      <span class="pin" style="top:10px"></span>Dralventorix Australia Pty Ltd<br>
      <span style="display:block;line-height:10px">14 Tarnwick Close<br>Orrin Vale<br>WA 6190, Australia</span>
      <span class="pin" style="top:56px"></span>+61 8 9000 4417 &nbsp;&nbsp; +61 8 9000 4418<br>
      <span class="pin" style="top:68px"></span>info@dralventorix.com.au
    </div>
    <p class="abs footnote">© 2015 Panelcrest. All rights reserved.</p>
    <div class="abs top-btn"><svg width="11" height="11" viewBox="0 0 11 11"><path d="M3 6.5l2.5-2.5 2.5 2.5" fill="none" stroke="#b3d233"/></svg></div>
    <div class="abs socials" style="left:439px;top:234px"><span></span><span></span><span></span><span></span><span></span></div>
  </section>

</div>
</body>
</html>
```